Business Card Design Project

Doctor, Pain Management. Need a new business card design with appointment info on the back. New address is 18 Corvell Road, Suite 304, Brisdale, NJ 07391. Right now I believe the rest of the information is staying the same.

```html
<!DOCTYPE html>
<html lang="en">
<head>
<meta charset="utf-8">
<title>Steadfast Pain Care – Business Card</title>
<link rel="stylesheet" href="https://fonts.googleapis.com/css2?family=Crimson+Text:wght@400;600&family=Open+Sans:ital,wght@0,400;0,700;1,400&display=swap">
<style>
  :root {
    --page-bg: #e8e5e0;
    --card-dark: #1d1e20;
    --card-dark-soft: #34363a;
    --card-blue: #7dcbf6;
    --card-blue-deep: #5fb9ee;
    --accent-yellow: #e6d41c;
    --ink: #141414;
    --ink-soft: #3a3a3a;
    --paper: #ffffff;
    --rule: #777777;
  }
  * { box-sizing: border-box; margin: 0; padding: 0; }
  html, body {
    width: 1200px; height: 950px; overflow: hidden;
    background: var(--page-bg);
  }
  .sheet {
    position: relative; width: 1200px; height: 950px;
  }
  .card {
    position: absolute; left: 250px; width: 700px; height: 400px;
    border-radius: 4px; overflow: hidden;
    box-shadow: 0 6px 18px rgba(0,0,0,.18);
  }
  .card-front { top: 50px; background: var(--card-blue); }
  .card-back { top: 500px; background: var(--paper); font-family: "Open Sans", Arial, sans-serif; color: var(--ink); }

  .front-art { position: absolute; inset: 0; }

  .brand {
    position: absolute; left: 70px; top: 150px;
    display: flex; align-items: center; gap: 14px;
  }
  .brand-mark {
    width: 44px; height: 44px; border-radius: 50%;
    background: var(--card-blue);
  }
  .brand-name {
    font-family: "Crimson Text", Georgia, serif;
    font-size: 30px; font-weight: 400; color: var(--accent-yellow);
    letter-spacing: .5px;
  }

  .contact {
    position: absolute; right: 34px; top: 52px;
    text-align: right;
    font-family: "Crimson Text", Georgia, serif;
    font-size: 17px; line-height: 22px; color: var(--ink);
  }

  .doctor {
    position: absolute; left: 130px; top: 296px;
    font-family: "Crimson Text", Georgia, serif; color: var(--ink-soft);
  }
  .doctor-name { font-size: 23px; line-height: 26px; }
  .doctor-title { font-size: 17px; line-height: 21px; }
  .doctor-address { font-size: 15px; line-height: 19px; }

  .appointment { position: absolute; inset: 0; padding: 34px 46px; }
  .appointment-title {
    text-align: center; font-size: 26px; font-weight: 700; margin-bottom: 22px;
  }
  .field {
    display: flex; align-items: flex-end; gap: 8px;
    font-size: 17px; height: 40px;
  }
  .field-line {
    flex: 1; border-bottom: 2px dotted var(--rule); height: 20px;
  }
  .field-suffix { font-size: 12px; }
  .days {
    display: flex; justify-content: space-between;
    font-size: 16px; margin: 18px 0 6px;
  }
  .day { display: flex; align-items: center; gap: 5px; }
  .checkbox {
    width: 16px; height: 16px; border: 1.5px solid var(--ink-soft);
  }
  .notice {
    margin-top: 30px; font-size: 13px; font-style: italic;
    text-align: center; line-height: 18px; color: var(--ink-soft);
  }
</style>
</head>
<body>
<main class="sheet">

  <section class="card card-front" aria-label="Business card front">
    <svg class="front-art" viewBox="0 0 700 400" width="700" height="400" aria-hidden="true">
      <defs>
        <linearGradient id="darkPanel" x1="0" y1="0" x2="1" y2="1">
          <stop offset="0" stop-color="var(--card-dark-soft)"/>
          <stop offset="0.5" stop-color="var(--card-dark)"/>
          <stop offset="1" stop-color="var(--card-dark)"/>
        </linearGradient>
        <linearGradient id="bluePanel" x1="0" y1="0" x2="0" y2="1">
          <stop offset="0" stop-color="var(--card-blue)"/>
          <stop offset="1" stop-color="var(--card-blue-deep)"/>
        </linearGradient>
      </defs>
      <rect width="700" height="400" fill="url(#bluePanel)"/>
      <path d="M0,0 H440 C400,50 380,130 360,228 C320,262 230,275 140,290 C80,300 40,325 0,360 Z" fill="url(#darkPanel)"/>
      <path d="M440,0 C400,50 380,130 360,228 C320,262 230,275 140,290 C80,300 40,325 0,360" fill="none" stroke="var(--accent-yellow)" stroke-width="4"/>
    </svg>

    <div class="brand">
      <span class="brand-mark"></span>
      <span class="brand-name">Steadfast Pain Care</span>
    </div>

    <address class="contact">
      P. 973.555.0142<br>
      F. 973.555.0148<br>
      frontdesk.service@steadfastpc.com<br>
      www.steadfastpc.com
    </address>

    <div class="doctor">
      <p class="doctor-name">Lianmei Soren, M.D., Ph.D.</p>
      <p class="doctor-title">Board Certified Anesthesiologist</p>
      <p class="doctor-address">18 Corvell Road, Suite 304</p>
      <p class="doctor-address">Brisdale, NJ 07391</p>
    </div>
  </section>

  <section class="card card-back" aria-label="Business card back">
    <div class="appointment">
      <h2 class="appointment-title">Next Appointment</h2>
      <div class="field"><span>Name :</span><span class="field-line"></span></div>
      <div class="field"><span>Date :</span><span class="field-line"></span></div>
      <div class="days">
        <span class="day">Mon <span class="checkbox"></span></span>
        <span class="day">Tue <span class="checkbox"></span></span>
        <span class="day">Wed <span class="checkbox"></span></span>
        <span class="day">Thu <span class="checkbox"></span></span>
        <span class="day">Fri <span class="checkbox"></span></span>
        <span class="day">Sat <span class="checkbox"></span></span>
      </div>
      <div class="field"><span>Time :</span><span class="field-line"></span><span class="field-suffix">AM/PM</span></div>
      <p class="notice">Please give 24 hours notice if you are unable to keep your appointment or<br>a cancellation fee may be charged.</p>
    </div>
  </section>

</main>
</body>
</html>
```